American cannabis tech company business card design

Pavrel.com is seeking a modern, professional, and brand-aligned business card that represents our company and its core values: Mission, Story, Values, and Impact. As an innovative cannabis company, we want a business card that is not only visually appealing but also serves as a representation of who we are and what we stand for.

Project Scope: Design a double-sided business card that integrates our brand identity and core values. Incorporate our key brand elements, ensuring a sleek and contemporary aesthetic. Visually reflect our core values (Mission, Story, Values, Impact) in a way that is engaging yet professional.

Target Market(s)

Vendors, third parties,

Contact Information for Business Card

Contact details (name, title, email, phone, website, etc.)

Font styles to use
Other font styles liked:
• Caslon, Centra

Colors

Designer to choose colors to be used in the design.

Requirements
Must have
• Pavrel.com logo and branding A creative yet clean way to integrate our core values (Mission, Story, Values, Impact) Modern typography and a well-structured layout
Nice to have
• forest green, grey, white, black
Should not have
• references to marijuana, leafs, plants, or related product

```html
<!DOCTYPE html>
<html lang="en">
<head>
<meta charset="utf-8">
<title>Pavrel.com Business Card</title>
<link rel="stylesheet" href="https://fonts.googleapis.com/css2?family=Montserrat:wght@400;500;600;800&display=swap">
<style>
  :root {
    --canvas: #4a4b4d;
    --forest: #18331a;
    --leaf-green: #2e9a35;
    --white: #ffffff;
    --ink: #183036;
  }
  html, body {
    margin: 0;
    padding: 0;
    width: 1200px;
    height: 1200px;
    overflow: hidden;
    background: var(--canvas);
    font-family: "Montserrat", sans-serif;
  }
  .canvas {
    position: relative;
    width: 1200px;
    height: 1200px;
  }
  .card {
    position: absolute;
    left: 250px;
    width: 700px;
    height: 400px;
    border-radius: 28px;
    overflow: hidden;
    box-shadow: 0 14px 30px rgba(0,0,0,0.35);
  }
  .card-front {
    top: 150px;
    background: var(--white);
  }
  .card-back {
    top: 650px;
    background: var(--forest);
    border: 3px solid var(--leaf-green);
    box-sizing: border-box;
  }
  .wave {
    position: absolute;
    inset: 0;
    width: 700px;
    height: 400px;
  }
  .wordmark-front {
    position: absolute;
    top: 80px;
    right: 70px;
    margin: 0;
    font-size: 62px;
    font-weight: 800;
    letter-spacing: 1px;
    line-height: 1;
    color: var(--forest);
  }
  .identity {
    position: absolute;
    left: 48px;
    top: 110px;
    color: var(--ink);
  }
  .full-name {
    margin: 0;
    font-size: 34px;
    font-weight: 600;
    letter-spacing: 0.5px;
    line-height: 1;
  }
  .job-title {
    margin: 4px 0 0 22px;
    font-size: 20px;
    font-weight: 400;
    letter-spacing: 1px;
    line-height: 1.2;
  }
  .contacts {
    list-style: none;
    margin: 14px 0 0 40px;
    padding: 0;
  }
  .contacts li {
    display: flex;
    align-items: center;
    gap: 10px;
    font-size: 19px;
    font-weight: 500;
    line-height: 28px;
  }
  .contacts svg {
    width: 20px;
    height: 20px;
    fill: var(--forest);
  }
  .wordmark-back {
    position: absolute;
    inset: 0;
    display: flex;
    align-items: center;
    justify-content: center;
    margin: 0;
    font-size: 110px;
    font-weight: 800;
    letter-spacing: 2px;
    color: var(--white);
  }
</style>
</head>
<body>
<main class="canvas">

  <section class="card card-front" aria-label="Business card front">
    <svg class="wave" viewBox="0 0 700 400" aria-hidden="true">
      <path fill="#2e9a35" d="M0,392 C120,318 250,316 400,304 C560,292 650,246 700,140 L700,400 L0,400 Z"/>
      <path fill="#ffffff" d="M18,400 C134,330 262,328 406,316 C566,304 654,262 700,160 L700,400 Z"/>
      <path fill="#18331a" d="M38,400 C150,340 272,338 410,326 C570,314 658,276 700,176 L700,400 Z"/>
    </svg>

    <h1 class="wordmark-front">PAVREL</h1>

    <div class="identity">
      <h2 class="full-name">FULL NAME</h2>
      <p class="job-title">TITLE</p>
      <ul class="contacts">
        <li>
          <svg viewBox="0 0 24 24"><path d="M6.6 10.8a15.1 15.1 0 0 0 6.6 6.6l2.2-2.2a1 1 0 0 1 1-.25 11.4 11.4 0 0 0 3.6.57 1 1 0 0 1 1 1V20a1 1 0 0 1-1 1A17 17 0 0 1 3 4a1 1 0 0 1 1-1h3.5a1 1 0 0 1 1 1c0 1.25.2 2.450.57 3.57a1 1 0 0 1-.25 1z"/></svg>
          (000) 000 0000
        </li>
        <li>
          <svg viewBox="0 0 24 24"><path d="M2 5h20v14H2z M4 7v.4l8 5.2 8-5.2V7z" fill-rule="evenodd"/></svg>
          email@company.com
        </li>
        <li>
          <svg viewBox="0 0 24 24"><path d="M12 2a10 10 0 1 0 0 20 10 10 0 0 0 0-20zm0 2c.9 1.1 1.7 2.9 2 5h-4c.3-2.1 1.1-3.9 2-5zM4.3 11h3.7c0 .7.1 1.4.2 2H4.3a8 8 0 0 1 0-2zm5.7 0h4a14 14 0 0 1-.1 2h-3.8a14 14 0 0 1-.1-2zm6 0h3.7a8 8 0 0 1 0 2h-3.9c.1-.6.2-1.3.2-2zM10.1 15h3.8c-.4 2-1.1 3.8-1.9 5-.8-1.2-1.500-3-1.9-5z"/></svg>
          www.company.com
        </li>
      </ul>
    </div>
  </section>

  <section class="card card-back" aria-label="Business card back">
    <h2 class="wordmark-back">PAVREL</h2>
  </section>

</main>
</body>
</html>
```